Veldmark Supplies Business Card

Professional business card that stand out to our potential customers. Front and back with clean modern design

Industry/Entity Type

Oil and gas

Contact Information for Business Card

Name, address, website , office phone and cell number

Requirements
Must have
• Editable files for each employee

```html
<!DOCTYPE html>
<html lang="en">
<head>
<meta charset="utf-8">
<title>Veldmark Supplies Business Card</title>
<link href="https://fonts.googleapis.com/css2?family=Montserrat:wght@400;500;700&display=swap" rel="stylesheet">
<style>
  :root {
    --backdrop: #d3d8d9;
    --paper: #f2f2f0;
    --brand-red: #ec2227;
    --brand-blue: #1fb3d2;
    --ink: #2b2b2b;
  }
  * { box-sizing: border-box; margin: 0; padding: 0; }
  html, body { width: 1200px; height: 881px; overflow: hidden; }
  body {
    background: var(--backdrop);
    font-family: "Montserrat", Arial, sans-serif;
    color: var(--ink);
    display: flex;
    align-items: center;
    justify-content: center;
    gap: 40px;
  }
  .card {
    width: 520px;
    height: 297px;
    background: var(--paper);
    border-bottom: 4px solid var(--brand-red);
    position: relative;
    display: flex;
  }
  .wordmark {
    display: flex;
    align-items: center;
    gap: 10px;
    color: var(--brand-red);
    font-weight: 700;
    text-transform: uppercase;
    letter-spacing: 0.06em;
  }
  .wordmark-square {
    width: 18px; height: 18px;
    background: var(--brand-blue);
    flex: none;
  }
  .card-front .brand-side {
    width: 240px;
    display: flex;
    align-items: center;
    justify-content: center;
    font-size: 17px;
  }
  .divider {
    width: 2px;
    background: var(--brand-red);
    margin: 40px 0;
  }
  .details {
    padding: 42px 0 0 28px;
  }
  .person-name {
    font-size: 25px;
    font-weight: 700;
    letter-spacing: 0.02em;
    line-height: 1;
  }
  .person-name .first { color: var(--brand-red); }
  .person-name .last { color: var(--brand-blue); }
  .person-role { font-size: 12px; margin: 6px 0 12px; }
  .address { font-size: 12px; line-height: 1.45; margin-bottom: 10px; }
  .contact-list { list-style: none; font-size: 12px; line-height: 1.6; }
  .contact-list li { display: flex; align-items: center; gap: 8px; }
  .contact-list svg { width: 11px; height: 11px; fill: var(--brand-red); flex: none; }
  .card-back {
    align-items: center;
    justify-content: center;
    font-size: 24px;
  }
  .card-back .wordmark-square { width: 24px; height: 24px; }
</style>
</head>
<body>
  <section class="card card-front" aria-label="Business card front">
    <div class="brand-side">
      <div class="wordmark"><span class="wordmark-square"></span>Veldmark Supplies</div>
    </div>
    <div class="divider"></div>
    <div class="details">
      <h1 class="person-name"><span class="first">DANIEL</span> <span class="last">ROURKE</span></h1>
      <p class="person-role">Managing Director</p>
      <p class="address">412 N.Calloway Suite 5<br>Midland, Tx 79701</p>
      <ul class="contact-list">
        <li><svg viewBox="0 0 12 12" aria-hidden="true"><path d="M2 1h3l1 3-2 1c1 2 2 3 3 3l1-2 3 1v3c-6 1-10-3-9-9z"/></svg>(555)214-0387</li>
        <li><svg viewBox="0 0 12 12" aria-hidden="true"><path d="M3 0h6v12H3zM4 1v9h4V1z"/></svg>555 302 118</li>
        <li><svg viewBox="0 0 12 12" aria-hidden="true"><path d="M0 2h12v8H0zM1 3l5 4 5-4z"/></svg>sales@veldmarksupplies.com</li>
        <li><svg viewBox="0 0 12 12" aria-hidden="true"><circle cx="6" cy="6" r="6"/></svg>www.veldmarksupplies.com</li>
      </ul>
    </div>
  </section>
  <section class="card card-back" aria-label="Business card back">
    <div class="wordmark"><span class="wordmark-square"></span>Veldmark Supplies</div>
  </section>
</body>
</html>
```